Tiny Sprout brochure

A brochure or rack card to give expecting parents an idea of the cost savings and enviornmental benefits to cloth diapering their kids. Also let them know its not hard like it was years ago!
Updates

Is anyone working on this? I sent the brief out last week and haven't gotten any submissions. Is my brief lacking information? PLEASE message me if you have questions!

Thanks

Molly

Reason: I have only received one submission!

Target Market(s)

parents

Requirements
Must have
• rack card with front and back OR tri fold brochure

a "why cloth?" section- you don't have to include ALL of the facts I included on my attachment, just a few. I really want to stress the money saved and enviornmenal benefits
pictures/logos of the brands I'm selling
my logo
contact info- www.tinysproutnestling.example and molly@tinysproutnestling.example

a "green" feel, but also want to setress that its not hard like when our parents cloth diapered with safety pins and rubber pants
Should not have
• I

```html
<!DOCTYPE html>
<html lang="en">
<head>
<meta charset="utf-8">
<title>Tiny Sprout – Why Cloth? Rack Card</title>
<link rel="stylesheet" href="https://fonts.googleapis.com/css2?family=Archivo+Black&family=Arimo:wght@400;700&display=swap">
<style>
  :root {
    --sky-top: #f4f9fd;
    --sky-mid: #cfe3f3;
    --sky-deep: #a9cbe7;
    --frame: #ffffff;
    --headline-blue: #1d6fb8;
    --emphasis-blue: #1f66ad;
    --offer-purple: #7d2b8b;
    --body-ink: #3b3b3b;
    --leaf-light: #a6d24a;
    --leaf-mid: #7fbf3a;
    --leaf-deep: #4f9b2c;
    --muted: #8a8f94;
    --strip-bg: #ffffff;
    --page-bg: #e9f1f7;
  }
  * { box-sizing: border-box; margin: 0; padding: 0; }
  html, body { width: 1200px; height: 2700px; overflow: hidden; }
  body {
    background: var(--page-bg);
    font-family: "Arimo", Arial, sans-serif;
    color: var(--body-ink);
    position: relative;
  }
  .card-panel {
    position: absolute;
    left: 28px; top: 28px;
    width: 1144px; height: 2370px;
    border: 10px solid var(--frame);
    border-radius: 28px;
    background: linear-gradient(180deg, var(--sky-top) 0%, var(--sky-mid) 45%, var(--sky-deep) 100%);
    overflow: hidden;
    box-shadow: 0 4px 14px rgba(40, 80, 120, 0.18);
  }
  .leaf-wave {
    position: absolute;
    left: 0; top: 1500px;
    width: 1124px; height: 850px;
  }
  .brand-block {
    position: absolute;
    top: 70px; left: 0; width: 100%;
    text-align: center;
  }
  .brand-name {
    display: inline-flex;
    align-items: center;
    gap: 22px;
    font-family: "Archivo Black", "Arial Black", sans-serif;
    font-size: 104px;
    color: var(--leaf-deep);
    letter-spacing: -1px;
    line-height: 1;
  }
  .brand-dot {
    width: 84px; height: 84px;
    border-radius: 50%;
    background: var(--leaf-mid);
  }
  .brand-tagline {
    display: inline-block;
    margin-top: 18px;
    padding: 10px 40px;
    background: var(--leaf-mid);
    color: #ffffff;
    font-family: "Archivo Black", "Arial Black", sans-serif;
    font-size: 34px;
    letter-spacing: 2px;
    border-radius: 8px;
  }
  .card-copy {
    position: absolute;
    top: 480px; left: 80px;
    width: 964px;
    font-size: 29px;
    line-height: 1.22;
  }
  .section-title {
    font-family: "Archivo Black", "Arial Black", sans-serif;
    font-size: 92px;
    color: var(--headline-blue);
    line-height: 1;
    display: inline;
    letter-spacing: -1px;
  }
  .intro { margin-bottom: 6px; }
  .savings-callout {
    font-family: "Archivo Black", "Arial Black", sans-serif;
    font-size: 58px;
    color: var(--emphasis-blue);
    line-height: 1.1;
  }
  .fact { margin-top: 30px; }
  .em-blue {
    color: var(--emphasis-blue);
    font-weight: 700;
    font-size: 36px;
  }
  .em-strong { font-weight: 700; }
  .offer-title {
    font-family: "Archivo Black", "Arial Black", sans-serif;
    font-size: 66px;
    color: var(--offer-purple);
    margin-top: 60px;
    line-height: 1;
  }
  .offer-list { margin-top: 10px; font-size: 30px; }
  .site-line {
    position: absolute;
    left: 0; width: 100%;
    top: 2230px;
    display: flex; align-items: center; justify-content: center; gap: 24px;
    font-size: 26px;
    color: var(--muted);
  }
  .site-line::before, .site-line::after {
    content: ""; display: block; width: 260px; height: 2px; background: var(--muted); opacity: .6;
  }
  .partner-strip {
    position: absolute;
    left: 0; top: 2440px;
    width: 1200px; height: 260px;
    background: var(--strip-bg);
    display: grid;
    grid-template-columns: repeat(3, 1fr);
    grid-template-rows: repeat(2, 1fr);
    align-items: center;
    justify-items: center;
    padding: 20px 70px;
    font-family: "Archivo Black", "Arial Black", sans-serif;
  }
  .partner { font-size: 46px; line-height: 1; }
  .partner--leafnest { color: #4f9b2c; }
  .partner--rinse { color: #2c6e2f; font-size: 40px; }
  .partner--plum { color: #b3262e; }
  .partner--pouchly { color: #2f6fb0; font-size: 42px; }
  .partner--clover { color: #4f9b2c; font-size: 30px; grid-column: 2 / 4; }
</style>
</head>
<body>
  <main class="card-panel">
    <svg class="leaf-wave" viewBox="0 0 1124 850" preserveAspectRatio="none" aria-hidden="true">
      <path d="M0 430 C 300 300, 700 260, 1124 0 L1124 850 L0 850 Z" fill="var(--leaf-light)" opacity="0.75"/>
      <path d="M0 560 C 380 430, 760 420, 1124 200 L1124 850 L0 850 Z" fill="var(--leaf-mid)" opacity="0.55"/>
      <path d="M0 700 C 400 620, 800 600, 1124 480 L1124 850 L0 850 Z" fill="#cfe3f3" opacity="0.35"/>
    </svg>

    <header class="brand-block">
      <div class="brand-name"><span class="brand-dot"></span>Tiny Sprout</div><br>
      <div class="brand-tagline">NATURAL BABY PRODUCTS</div>
    </header>

    <section class="card-copy">
      <p class="intro"><span class="section-title">WHY CLOTH?</span> I initially started doing my research on cloth diapers when I was pregnant with our first son. After realizing that I could</p>
      <p class="savings-callout">SAVE BETWEEN $500-$2000</p>
      <p>(depending on the type of diaper used) <span class="em-strong">per child</span> if I cloth diapered, the decision was a no brainer to me... Upon researching the cost benefits of cloth diapering, I made some other helpful discoveries that made me a cloth diaper fanatic!</p>

      <p class="fact">-Disposable diapers are so wasteful. They make up over 30% of what is in our landfills today. And all of those diapers can take as long as <span class="em-blue">500 years to decompose.</span> Your cute little baby will go through <span class="em-blue">over a ton of disposable diapers</span> by the time they are ready to potty train!</p>

      <p class="fact">-Disposable diapers <span class="em-blue">contain a chemical called Dioxin</span>, which is extremely toxic and <span class="em-blue">cancer causing</span>, as reported by the Environmental Safety Board. Its been banned in most other countries.</p>

      <p class="fact">-Disposable diapers can actually cause diaper rash. The chemicals used by diaper manufacturers to make them absorbent of moisture are extremely harsh on your baby sensitive skin!</p>

      <p class="fact"><span class="em-blue">-Disposable diapers have been linked to infertility later in life for men.</span> In May, 2000, the Journal of Child Health Studies published a study which showed that scrotal <span class="em-blue">temperature in boys is increased</span> while wearing diapers and that prolonged disposable diaper use can completely destroy the physiological cooling mechanism important for sperm production.</p>

      <h2 class="offer-title">WE OFFER</h2>
      <p class="offer-list">•custom packages to fit your full time or part time diapering needs •incentive program •gift registry •cute prints •customer care to help you choose which diaper is right for you</p>
    </section>

    <p class="site-line">www.tinysproutnestling.example</p>
  </main>

  <footer class="partner-strip">
    <span class="partner partner--leafnest">Leafnest</span>
    <span class="partner partner--rinse">Rinse Meadow</span>
    <span class="partner partner--plum">Plum Lantern</span>
    <span class="partner partner--pouchly">Pouchly Care</span>
    <span class="partner partner--clover">Soft Clover Organics</span>
  </footer>
</body>
</html>
```